All-Natural Head Lice Removal company

I need a business card with my pre-existing logo. We are a new company located in Portland Oregon that goes into peoples homes to help with head lice removal. My products and approach are all- natural and also will be around children.On my current logo we used Teal Bl and the color Green. I am open to new ideas just want it simple and creative

Target Market(s)

my biggest market is families of school aged children

Industry/Entity Type

Business

Contact Information for Business Card

see upload for details from previous business card

Font styles to use
Serif

Colors
33a6d7
9bcb3b
f37122

Requirements
Must have
• Basic information/ logo put into a creative format that is catching to the eye
Nice to have
• creative

```html
<!DOCTYPE html>
<html lang="en">
<head>
<meta charset="utf-8">
<title>Clear Comb Business Card</title>
<link rel="stylesheet" href="https://fonts.googleapis.com/css2?family=Roboto+Slab:wght@400;700&display=swap">
<style>
  :root {
    --backdrop: #e6e3de;
    --card: #ffffff;
    --blue: #33a6d7;
    --blue-deep: #2a8fc8;
    --green: #9bcb3b;
    --ink: #2b2b2b;
    --shadow: rgba(0,0,0,0.18);
  }
  * { margin: 0; padding: 0; box-sizing: border-box; }
  html, body {
    width: 1200px; height: 913px; overflow: hidden;
    background: var(--backdrop);
    font-family: "Roboto Slab", Georgia, serif;
    color: var(--ink);
  }
  .stage { position: relative; width: 1200px; height: 913px; }
  .card {
    position: absolute; width: 520px; height: 298px;
    background: var(--card); border-radius: 16px; overflow: hidden;
    box-shadow: 0 10px 24px var(--shadow);
  }
  .card--front { left: 50px; top: 200px; }
  .card--back { left: 630px; top: 415px; }

  .front-band { position: absolute; inset: 0; width: 100%; height: 100%; }
  .person { position: absolute; left: 34px; top: 104px; color: var(--ink); }
  .person__name { font-size: 21px; font-weight: 700; letter-spacing: 0.5px; text-transform: uppercase; }
  .person__role { font-size: 12px; color: #fff; text-transform: uppercase; margin-top: 2px; }

  .contact { position: absolute; left: 92px; top: 192px; list-style: none; font-size: 13px; color: var(--ink); }
  .contact li { display: flex; align-items: center; gap: 7px; height: 19px; }
  .contact svg { width: 11px; height: 11px; flex: none; }

  .brand { display: flex; align-items: center; gap: 10px; font-weight: 700; color: var(--ink); white-space: nowrap; }
  .brand__dot { border-radius: 50%; background: var(--green); flex: none; }
  .brand--small { position: absolute; left: 300px; top: 72px; font-size: 26px; }
  .brand--small .brand__dot { width: 34px; height: 34px; }
  .front-tagline { position: absolute; left: 318px; top: 130px; font-size: 13px; line-height: 1.35; color: var(--ink); }

  .back-content { position: absolute; inset: 0; display: flex; flex-direction: column; align-items: center; justify-content: center; text-align: center; }
  .brand--large { font-size: 46px; margin-bottom: 22px; }
  .brand--large .brand__dot { width: 64px; height: 64px; }
  .back-tagline { font-size: 15px; line-height: 1.3; color: var(--blue); }
  .back-web { font-size: 14px; font-weight: 700; margin-top: 6px; color: var(--ink); }
</style>
</head>
<body>
<main class="stage">
  <section class="card card--front" aria-label="Card front">
    <svg class="front-band" viewBox="0 0 520 298" preserveAspectRatio="none" aria-hidden="true">
      <defs>
        <linearGradient id="bandFill" x1="0" y1="0" x2="0" y2="1">
          <stop offset="0" stop-color="#6cc3ea"/>
          <stop offset="1" stop-color="#2a8fc8"/>
        </linearGradient>
      </defs>
      <path d="M0,0 L178,0 Q318,118 266,298 L0,298 Z" fill="url(#bandFill)"/>
      <path d="M178,0 Q318,118 266,298" fill="none" stroke="#ffffff" stroke-width="4"/>
      <path d="M186,0 Q326,118 274,298" fill="none" stroke="#9bcb3b" stroke-width="4"/>
    </svg>
    <div class="person">
      <p class="person__name">Maren Holloway</p>
      <p class="person__role">Owner</p>
    </div>
    <ul class="contact">
      <li><svg viewBox="0 0 12 12"><path d="M2.5 1 L4.5 1 L5.3 3.5 L4 4.5 Q5 7 7.5 8 L8.5 6.7 L11 7.5 L11 9.5 Q10.5 11 9 11 Q1 10 1 3 Q1 1.5 2.5 1 Z" fill="#fff"/></svg>1-855-555-NITS (6487)</li>
      <li><svg viewBox="0 0 12 12"><rect x="1" y="2.5" width="10" height="7" fill="none" stroke="#fff" stroke-width="1.2"/><path d="M1 2.5 L6 6.5 L11 2.5" fill="none" stroke="#fff" stroke-width="1.2"/></svg>maren@clearcomb.com</li>
      <li><svg viewBox="0 0 12 12"><circle cx="6" cy="6" r="5" fill="none" stroke="#fff" stroke-width="1.2"/><path d="M1 6 H11 M6 1 Q3 6 6 11 Q9 6 6 1" fill="none" stroke="#fff" stroke-width="1"/></svg>www.clearcomb.com</li>
    </ul>
    <div class="brand brand--small"><span class="brand__dot"></span>Clear Comb</div>
    <p class="front-tagline">All Natural In-Home<br>Lice Removal Services</p>
  </section>

  <section class="card card--back" aria-label="Card back">
    <div class="back-content">
      <div class="brand brand--large"><span class="brand__dot"></span>Clear Comb</div>
      <p class="back-tagline">Try Clear Comb Today and Be Lice Free Tomorrow!<br>All Natural In-Home Lice Removal Services</p>
      <p class="back-web">www.clearcomb.com</p>
    </div>
  </section>
</main>
</body>
</html>
```